Belvascotravel.com web design project + logo design

Hi,

We are a Russian online tour operator - sunkettle.com

We are looking to tranmsfer our domain to belvascotravel.com. The website and logo need to be belvascoesque - we are not looking to change our functionality, but we need to make the website much more attracitve to clients, much more wild looking but at the same time remaining a professional travel company.

The main concept of the website should be innovative travel (as belvasco was an innovator). Alternatively, you could go down the artist route and go down the draw / design your own tour road.

On our website the customer is able to combine travel services (hotels, flights, Visa services, and soon chauffeur, car rental etc...) put it into their basket (the basket definitely has to look better than it is at the moment) and pay for it in one go by card.

We are also stressin our customer support with web chat, call centre etc... (call centre number at the top of the page)

We aim to provide an easy user experience, but we need to make it have some more style, so I will be waiting for what you guys can come up with.
Let me know if you have any questions - skype is: mrdolbarin

Industry/Entity Type

It Company

Requirements
Must have
• It is quite a simple task - to take the existing website sunkettle.com and belvascosize it to create belvascotravel.com, the functionality of the website will remain the same and there are not many pages in the website. Homepage, Checkout step1, Checkout step 2 (you can view both of these if you select a service) and the generic pages for T&C''s, Privacy policy etc...

IMPORTANT UPDATE

We are also looking at how the search results will look in the designs, (please do a search on our website for hotel / flight)

```html
<!DOCTYPE html>
<html lang="en">
<head>
<meta charset="utf-8">
<title>Belvasco Travels</title>
<link href="https://fonts.googleapis.com/css2?family=Mulish:wght@400;600;700&family=Arimo:wght@400;700&display=swap" rel="stylesheet">
<style>
:root{
  --sky:#d3ebf8;
  --sky-deep:#c2e2f4;
  --blue:#1b8fd6;
  --blue-dark:#0c6fb8;
  --cyan-text:#1aa0dc;
  --navy:#1d3c5a;
  --green:#2a8a2e;
  --grey-text:#6f7780;
  --ink:#2b2f33;
  --line:#4ab3e6;
}
*{box-sizing:border-box;margin:0;padding:0}
html,body{width:1200px;height:2579px;overflow:hidden}
body{position:relative;background:#f4f8fb;font-family:"Arimo",Arial,sans-serif;color:var(--ink)}

/* header */
.site-header{position:absolute;left:0;top:0;width:1200px;height:155px;background:linear-gradient(#d7edf9,#ffffff 45%)}
.brand{position:absolute;left:129px;top:62px;display:flex;align-items:center;gap:12px}
.brand-dot{width:34px;height:34px;border-radius:50%;background:var(--blue)}
.brand-name{font-family:"Mulish",sans-serif;font-weight:700;font-size:26px;color:var(--blue-dark)}
.help{position:absolute;left:920px;top:46px;width:170px}
.help-label{display:flex;align-items:center;gap:8px;font-family:"Mulish",sans-serif;font-size:18px;color:var(--navy)}
.help-phone{font-family:"Mulish",sans-serif;font-size:21px;color:var(--cyan-text);margin:4px 0 0 10px}
.contact-btn{position:absolute;left:944px;top:101px;width:108px;height:25px;border-radius:13px;background:linear-gradient(#3bb041,#23862a);color:#fff;font:700 12px/25px "Arimo",sans-serif;text-align:center}

/* nav */
.main-nav{position:absolute;left:0;top:155px;width:1200px;height:43px;background:linear-gradient(#3fb0ee,#1586d2)}
.nav-item{position:absolute;top:0;color:#fff;font:700 12.5px/43px "Mulish",sans-serif}
.nav-sep{position:absolute;top:10px;width:1px;height:23px;background:rgba(255,255,255,.35)}
.search-input{position:absolute;left:763px;top:162px;width:243px;height:29px;background:#fff;color:#b7bfc6;font-size:12.5px;line-height:29px;padding-left:14px}
.search-btn{position:absolute;left:1006px;top:162px;width:84px;height:29px;background:linear-gradient(#3a3a3a,#111);color:#fff;font:700 13px/29px "Arimo",sans-serif;text-align:center}

/* hero */
.hero-band{position:absolute;left:0;top:198px;width:1200px;height:507px;background:var(--sky)}
.hero-photo{position:absolute;left:112px;top:215px;width:978px;height:311px;background:linear-gradient(100deg,#4e7f8e 0%,#2fa0c0 30%,#4cc4d6 55%,#7ab4a5 80%,#8a8a6a 100%);box-shadow:0 6px 10px rgba(0,0,0,.15)}
.search-panel{position:absolute;left:497px;top:244px;width:546px;height:251px;background:#fff;border-radius:6px;box-shadow:0 3px 8px rgba(0,0,0,.25);border-bottom:6px solid var(--blue)}
.panel-title{position:absolute;left:20px;top:18px;font:600 17px/22px "Mulish",sans-serif;color:#222}
.f-label{position:absolute;width:70px;font-size:13px;line-height:26px;color:#333;text-align:right;white-space:nowrap}
.f-select{position:absolute;height:26px;border-radius:3px;background:linear-gradient(#f6f6f6,#dedede);border:1px solid #cfcfcf;font-size:11.5px;color:#555;line-height:24px;padding-left:26px}
.f-select::before{content:"";position:absolute;left:10px;top:8px;width:8px;height:8px;border:1.5px solid #3aa2dc;border-radius:50%}
.f-select::after{content:"";position:absolute;right:10px;top:10px;border:4px solid transparent;border-top:5px solid #444}
.check{position:absolute;font-size:11px;color:#444;display:flex;align-items:center;gap:8px}
.box{width:11px;height:11px;border:1px solid #aaa;background:#f3f3f3;font-size:9px;line-height:9px;text-align:center}
.avail-btn{position:absolute;left:399px;top:201px;width:130px;height:28px;background:linear-gradient(#3bad40,#22852a);color:#fff;font:700 13px/28px "Arimo",sans-serif;text-align:center;border-radius:2px}
.welcome-title{position:absolute;left:0;top:557px;width:1200px;text-align:center;font:400 27px "Mulish",sans-serif;color:#1f2a33}
.welcome-text{position:absolute;left:143px;top:605px;width:914px;text-align:center;font-size:13.2px;line-height:23px;color:var(--grey-text)}

/* content */
.content{position:absolute;left:112px;top:705px;width:978px;height:1580px;background:#fff;box-shadow:0 0 40px rgba(0,0,0,.12)}
.section-rule{position:absolute;height:5px;border-top:1.5px dotted var(--line);border-bottom:1.5px dotted var(--line)}
.section-title{position:absolute;text-align:center;white-space:nowrap;font:400 19px/24px "Mulish",sans-serif;color:var(--cyan-text);letter-spacing:.5px}
.svc-photo{position:absolute;width:127px;height:127px;border-radius:50%;border:5px solid #e6eef3;box-shadow:0 1px 4px rgba(0,0,0,.2)}
.svc-title{position:absolute;font:400 20px "Mulish",sans-serif;color:var(--green)}
.svc-text{position:absolute;width:270px;font-size:13.2px;line-height:20px;color:#555}
.read-more{position:absolute;font:700 13.2px "Arimo",sans-serif;color:var(--blue-dark)}
.detail-title{position:absolute;left:146px;font:400 20px "Mulish",sans-serif;color:var(--navy)}
.detail-text{position:absolute;left:146px;width:910px;font-size:13.2px;line-height:23px;color:var(--grey-text)}
.detail-list{position:absolute;left:148px;list-style:none}
.detail-list li{position:relative;padding-left:18px;height:30px;font-size:13.2px;color:var(--green)}
.detail-list li::before{content:"";position:absolute;left:0;top:6px;width:5px;height:5px;border-radius:50%;background:#1c3a55}

/* footer */
.site-footer{position:absolute;left:0;top:2326px;width:1200px;height:253px;background:var(--sky-deep)}
.f-col{position:absolute;top:32px}
.f-col h4{font:400 16px "Mulish",sans-serif;color:var(--blue-dark);margin-bottom:12px}
.f-col a{display:block;font-size:12.5px;line-height:15.5px;color:var(--blue);text-decoration:none}
.pay-badge{position:absolute;width:29px;height:20px;border-radius:3px;background:#fff;border:1px solid #9fc3dd}
.award{position:absolute;left:990px;top:2px}
.copyright{position:absolute;left:0;top:196px;width:1200px;text-align:center;font-size:12.5px;line-height:18px;color:#1d3a55}
</style>
</head>
<body>

<header class="site-header">
  <div class="brand"><span class="brand-dot"></span><span class="brand-name">belvascotravel.com</span></div>
  <div class="help">
    <div class="help-label">
      <svg width="14" height="14" viewBox="0 0 24 24"><path d="M6.6 10.8a15 15 0 006.6 6.6l2.2-2.2c.3-.3.7-.4 1-.2 1.1.4 2.3.6 3.6.6.6 0 1 .4 1 1V20c0 .6-.4 1-1 1C10.6 21 3 13.4 3 4c0-.6.4-1 1-1h3.5c.6 0 1 .4 1 1 0 1.3.2 2.5.6 3.6.1.3 0 .7-.2 1z" fill="#1d3c5a"/></svg>
      Need any Help
    </div>
    <div class="help-phone">0845 000 4127</div>
  </div>
  <div class="contact-btn">CONTACT US</div>
</header>

<nav class="main-nav">
  <span class="nav-item" style="left:132px">HOME</span>
  <span class="nav-sep" style="left:196px"></span>
  <span class="nav-item" style="left:220px">DESTINATIONS</span>
  <span class="nav-sep" style="left:335px"></span>
  <span class="nav-item" style="left:358px">ACTIVITES</span>
  <span class="nav-sep" style="left:447px"></span>
  <span class="nav-item" style="left:473px">TRIP STYLES</span>
  <span class="nav-sep" style="left:562px"></span>
  <span class="nav-item" style="left:588px">RESPONSIBLE TRAVEL</span>
</nav>
<div class="search-input">Search your dream place</div>
<div class="search-btn">SEARCH</div>

<section class="hero-band"></section>
<div class="hero-photo" role="img" aria-label="Two hikers resting on a rocky hillside above a turquoise bay"></div>
<form class="search-panel">
  <div class="panel-title">FIND THE RIGHT PLACE FOR YOUR<br>SUMMER HOLIDAY</div>
  <span class="f-label" style="left:0;top:81px">Откуда</span>
  <div class="f-select" style="left:79px;top:81px;width:182px">Select Any one</div>
  <span class="f-label" style="left:264px;top:81px">Куда</span>
  <div class="f-select" style="left:344px;top:81px;width:183px">Select Any one</div>
  <span class="f-label" style="left:0;top:120px">Туда</span>
  <div class="f-select" style="left:79px;top:120px;width:182px">Select Any one</div>
  <span class="f-label" style="left:264px;top:120px">Откуда</span>
  <div class="f-select" style="left:344px;top:120px;width:183px">Select Any one</div>
  <span class="f-label" style="left:18px;top:160px;width:78px">Пассажиры</span>
  <div class="f-select" style="left:103px;top:160px;width:144px">Select</div>
  <div class="f-select" style="left:254px;top:160px;width:133px">Select</div>
  <div class="f-select" style="left:395px;top:160px;width:132px">Select</div>
  <span class="f-label" style="left:4px;top:199px">Класс</span>
  <div class="f-select" style="left:81px;top:199px;width:101px">Select</div>
  <div class="check" style="left:199px;top:195px"><span class="box"></span>Обратно</div>
  <div class="check" style="left:199px;top:212px"><span class="box">✓</span>В одну сторону</div>
  <div class="avail-btn">View Availability</div>
</form>
<h1 class="welcome-title">Welcome to Belvasco Travels</h1>
<p class="welcome-text">Lorem Ipsum est simplement du faux texte employé dans la sition et la misen page avant impression. Le Lorem Ipsum est le faux texte standard de l'imprimerie depuis les années 1500, quand un peintre anonyme assembla ensemble des morceaux de texte pour réaliser un livre spécimen de polices de texte. Il n'a pas fait que survivre cinq siècles, mais s'est</p>

<main class="content">
  <span class="section-rule" style="left:13px;top:57px;width:385px"></span>
  <h2 class="section-title" style="left:398px;top:47px;width:180px">OUR SERVICES</h2>
  <span class="section-rule" style="left:578px;top:57px;width:385px"></span>

  <div class="svc-photo" style="left:31px;top:99px;background:linear-gradient(135deg,#dfe6ee,#2d4f7a)" role="img" aria-label="Passport and travel documents"></div>
  <h3 class="svc-title" style="left:185px;top:105px">Visa Services</h3>
  <p class="svc-text" style="left:189px;top:138px">Lorem Ipsum est simplement du faux texte employé dans la sition et la misen page avant impression.</p>
  <span class="read-more" style="left:189px;top:204px">Read More</span>

  <div class="svc-photo" style="left:514px;top:99px;background:linear-gradient(135deg,#6b7c8c,#1f4f8c)" role="img" aria-label="Flight attendant in uniform"></div>
  <h3 class="svc-title" style="left:667px;top:105px">Flight Service</h3>
  <p class="svc-text" style="left:669px;top:138px">Lorem Ipsum est simplement du faux texte employé dans la sition et la misen page avant impression.</p>
  <span class="read-more" style="left:669px;top:204px">Read More</span>

  <div class="svc-photo" style="left:31px;top:294px;background:linear-gradient(135deg,#7a3a3a,#e6ddd6)" role="img" aria-label="Hotel room with a made bed"></div>
  <h3 class="svc-title" style="left:191px;top:300px">Hoteling Service</h3>
  <p class="svc-text" style="left:194px;top:333px">Lorem Ipsum est simplement du faux texte employé dans la sition et la misen page avant impression.</p>
  <span class="read-more" style="left:194px;top:399px">Read More</span>

  <div class="svc-photo" style="left:514px;top:294px;background:linear-gradient(135deg,#2b2b2b,#8a7060)" role="img" aria-label="Driver at the wheel of a rental car"></div>
  <h3 class="svc-title" style="left:667px;top:300px">Car Rental Service</h3>
  <p class="svc-text" style="left:669px;top:333px">Lorem Ipsum est simplement du faux texte employé dans la sition et la misen page avant impression.</p>
  <span class="read-more" style="left:669px;top:399px">Read More</span>

  <span class="section-rule" style="left:18px;top:520px;width:325px"></span>
  <h2 class="section-title" style="left:343px;top:510px;width:290px">MORE ABOUT OUR SERVICE</h2>
  <span class="section-rule" style="left:633px;top:520px;width:330px"></span>
</main>

<h3 class="detail-title" style="top:1263px">Visa Service</h3>
<p class="detail-text" style="top:1305px">Lorem Ipsum est simplement du faux texte employé dans la sition et la misen page avant impression. Le Lorem Ipsum est le faux texte standard de l'imprimerie depuis les années 1500, quand un peintre anonyme assembla ensemble des morceaux de texte pour réaliser un livre spécimen de polices de texte. Il n'a pas fait que survivre cinq siècles, mais s'est aussi adapté à la bureautique informatique, sans que son contenu n'en soit modifié. Il a été popularisé dans les années 1960 grâce à la vente de feuilles Transferline contenant des passages du Lorem Ipsum, et, plus récemment, par son inclusion dans des applications de mise en page de texte, comme Pagesmith Layout.</p>
<ul class="detail-list" style="top:1443px">
  <li>Ensemble morceaux quand un peintre anonyme assembla</li>
  <li>Peintre anonyme assembla ensemble des morceaux quand un</li>
  <li>Quand peintre anonyme assembla ensemble des morceaux</li>
  <li>Anony assembla ensemble des morceaux quand un peintre</li>
</ul>

<h3 class="detail-title" style="top:1585px">Flight Service</h3>
<p class="detail-text" style="top:1627px">Lorem Ipsum est simplement du faux texte employé dans la sition et la misen page avant impression. Le Lorem Ipsum est le faux texte standard de l'imprimerie depuis les années 1500, quand un peintre anonyme assembla ensemble des morceaux de texte pour réaliser un livre spécimen de polices de texte. Il n'a pas fait que survivre cinq siècles, mais s'est aussi adapté à la bureautique informatique, sans que son contenu n'en soit modifié. Il a été popularisé dans les années 1960</p>
<ul class="detail-list" style="top:1739px">
  <li>Ensemble morceaux quand un peintre anonyme assembla</li>
  <li>Peintre anonyme assembla ensemble des morceaux quand un</li>
</ul>

<h3 class="detail-title" style="top:1826px">Hotelling Service</h3>
<p class="detail-text" style="top:1868px">Lorem Ipsum est simplement du faux texte employé dans la sition et la misen page avant impression. Le Lorem Ipsum est le faux texte standard de l'imprimerie depuis les années 1500, quand un peintre anonyme assembla ensemble des morceaux de texte pour réaliser un livre spécimen de polices de texte.</p>
<ul class="detail-list" style="top:1955px">
  <li>Ensemble morceaux quand un peintre anonyme assembla</li>
  <li>Peintre anonyme assembla ensemble des morceaux quand un</li>
</ul>

<h3 class="detail-title" style="top:2051px">Car Rental Service</h3>
<p class="detail-text" style="top:2093px">Lorem Ipsum est simplement du faux texte employé dans la sition et la misen page avant impression. Le Lorem Ipsum est le faux texte standard de l'imprimerie depuis les années 1500, quand un peintre anonyme assembla ensemble des morceaux de texte pour réaliser un livre spécimen de polices de texte.</p>
<ul class="detail-list" style="top:2182px">
  <li>Ensemble morceaux quand un peintre anonyme assembla</li>
  <li>Peintre anonyme assembla ensemble des morceaux quand un</li>
</ul>

<footer class="site-footer">
  <div class="f-col" style="left:139px"><h4>Destination</h4>
    <a>Europe</a><a>North America</a><a>South America</a><a>Africa</a><a>Asia</a><a>Australie</a></div>
  <div class="f-col" style="left:326px"><h4>Site Map</h4>
    <a>Home</a><a>Activites</a><a>Trip Styles</a><a>Responsible Travel</a></div>
  <div class="f-col" style="left:496px"><h4>Our guarantees</h4>
    <a>Money back guarantee</a><a>Low price guarantee</a></div>
  <div class="f-col" style="left:698px"><h4>Payment</h4>
    <a>Payment methods we accept</a><a>Open a business account</a><a>Schools and local authorities</a></div>

  <span class="pay-badge" style="left:947px;top:24px"></span>
  <span class="pay-badge" style="left:947px;top:52px"></span>
  <span class="pay-badge" style="left:947px;top:80px"></span>
  <span class="pay-badge" style="left:947px;top:108px"></span>
  <span class="pay-badge" style="left:947px;top:136px;height:12px"></span>
  <span class="pay-badge" style="left:889px;top:114px;width:40px;height:18px"></span>

  <svg class="award" width="80" height="144" viewBox="0 0 80 144">
    <path d="M0 0H80V144L40 122L0 144Z" fill="#1787cf"/>
    <text x="40" y="20" text-anchor="middle" fill="#fff" font-family="Arimo,sans-serif" font-size="10">Check out</text>
    <text x="40" y="32" text-anchor="middle" fill="#fff" font-family="Arimo,sans-serif" font-size="10">our awards!</text>
    <circle cx="40" cy="78" r="27" fill="#fff"/>
    <path d="M31 66h18v7a9 9 0 01-18 0zM38 82h4v6h5v4H33v-4h5z" fill="#1787cf"/>
  </svg>

  <p class="copyright">© 2003 - 2013 Belvasco Travels, 12 Harlow Lane, Millbrook, MB4 2QT Tel: 0845 000 4127<br>Company No: BTL4471 VAT Registration No: 604 218 335 Data Protection Reg: ZK55120478</p>
</footer>

</body>
</html>
```